Meridale Real Estate

We are looking for help with web design for a new company that is revolutionizing the real estate world on the listing side: by charing per hour for top level professional real estate services. We would like the concept to be simple, clean and easily understood.
Updates

We want this website to actually function, not just a static design.

Industry/Entity Type

Real Estate

```html
<!DOCTYPE html>
<html lang="en">
<head>
<meta charset="utf-8">
<title>Meridale Real Estate — Pros by the Hour</title>
<link href="https://fonts.googleapis.com/css2?family=Arimo:wght@400;700&family=Roboto+Condensed:wght@400;700&display=swap" rel="stylesheet">
<style>
:root{
  --teal:#0aa6ac;
  --teal-band:#02a9ae;
  --teal-soft:#5fd9de;
  --ink:#333;
  --muted:#666;
  --line:#d9d9d9;
  --btn-border:#c4c4c4;
  --footer:#2a2a2a;
  --footer-base:#1c1c1c;
  --footer-text:#a9a9a9;
  --white:#fff;
}
*{margin:0;padding:0;box-sizing:border-box}
html,body{width:782px;height:1200px;overflow:hidden;background:var(--white)}
body{position:relative;font-family:"Arimo",Arial,sans-serif;color:var(--ink)}
.abs{position:absolute}

/* header */
.site-header{left:0;top:0;width:782px;height:57px;background:var(--white);z-index:3}
.brand{left:115px;top:8px;width:54px;height:54px;border-radius:50%;background:var(--white);display:flex;align-items:center;justify-content:center;text-align:center;font-size:6.5px;line-height:8px;color:#b07a45;letter-spacing:.4px;z-index:4;text-transform:uppercase}
.ctrl{top:21px;height:17px;z-index:5;background:linear-gradient(#f1f1f1,#dedede);border:1px solid var(--btn-border);border-radius:2px;font-size:7.2px;color:#555;display:flex;align-items:center;padding-left:9px}
.ctrl svg{position:absolute;right:6px;top:4px}
.search-field{left:356px;width:139px}
.btn-login{left:502px;width:49px}
.btn-register{left:558px;width:60px}
.btn-help{left:625px;width:45px}

/* hero */
.hero{left:0;top:57px;width:782px;height:317px;background:linear-gradient(180deg,#4c8fd6 0%,#7fb6e6 30%,#9a8a6f 55%,#5a4630 78%,#2b2a2c 100%)}
.hero-arrow{top:197px;width:28px;height:28px;border:1.5px solid rgba(255,255,255,.35);border-radius:50%}
.search-mask{left:129px;top:312px;width:536px;height:46px;background:rgba(255,255,255,.85)}
.search-mask h2{position:absolute;left:14px;top:17px;font-family:"Roboto Condensed",sans-serif;font-weight:400;font-size:10.5px;line-height:12px;color:#333;white-space:nowrap}
.mask-select{top:14px;height:19px;width:121px;background:var(--white);border:1px solid #d5d5d5;font-size:6.2px;color:#777;display:flex;align-items:center;padding-left:10px;letter-spacing:.2px}
.mask-select svg{position:absolute;right:6px;top:4px}
.mask-submit{left:469px;top:14px;width:55px;height:19px;background:#555;border-radius:2px;color:var(--white);font-size:8px;display:flex;align-items:center;justify-content:center}

/* welcome */
.welcome-photo{left:112px;top:402px;width:190px;height:116px;background:linear-gradient(180deg,#5a6f9e 0%,#b78fa2 40%,#6c5f58 70%,#2f3f55 100%)}
.welcome-title{left:329px;top:401px;font-size:16px;font-weight:400;color:var(--teal)}
.welcome-text{left:329px;top:424px;width:326px;font-size:7px;line-height:15.6px;color:var(--muted)}
.divider{left:112px;top:542px;width:558px;height:1px;background:var(--line)}

/* offers */
.section-title{left:0;width:782px;text-align:center;font-weight:400}
.offers-title{top:560px;font-size:15.5px;color:var(--teal)}
.lead{left:136px;width:510px;text-align:center;font-size:7.2px;line-height:15.6px;color:var(--muted)}
.offers-lead{top:587px}
.pager{top:612px}
.offer{top:634px;width:127px}
.offer .photo{width:127px;height:108px}
.offer h3{margin-top:11px;font-size:7px;font-weight:700;color:#222;text-transform:uppercase}
.offer p{margin-top:5px;font-size:6.5px;line-height:11px;color:var(--muted)}
.offer .read{margin-top:6px;width:50px;height:17px;border:1px solid var(--btn-border);background:linear-gradient(#f4f4f4,#e2e2e2);border-radius:2px;font-size:6.2px;color:#555;display:flex;align-items:center;justify-content:center}

/* testimonials */
.testimonials{left:0;top:841px;width:782px;height:203px;background:var(--teal-band)}
.testimonials-title{top:862px;font-size:15px;color:var(--white)}
.testimonials-lead{top:888px;color:var(--white)}
.t-rule{left:116px;top:932px;width:550px;height:1px;background:rgba(255,255,255,.18)}
.avatar{top:947px;width:70px;height:70px;border-radius:50%}
.quote{top:949px;width:165px;color:var(--white)}
.quote h4{font-size:8.2px;font-weight:400}
.quote time{display:block;margin-top:5px;font-size:6.4px;font-style:italic;color:var(--teal-soft)}
.quote p{margin-top:4px;font-size:6.5px;line-height:12.8px}

/* footer */
.site-footer{left:0;top:1044px;width:782px;height:124px;background:var(--footer)}
.foot-col{top:1063px}
.foot-col h5{font-size:8.6px;font-weight:400;color:#e6e6e6;margin-bottom:6px}
.foot-col li{list-style:none;font-size:6px;color:var(--footer-text);line-height:14.1px}
.social{left:606px;top:1063px}
.social li{list-style:none;display:flex;align-items:center;height:20px;font-size:6px;color:var(--footer-text)}
.social i{display:block;width:13px;height:13px;border-radius:50%;background:#4a4a4a;margin-right:3px}
.footer-base{left:0;top:1168px;width:782px;height:32px;background:var(--footer-base);color:#e0e0e0;font-size:6.2px;font-weight:700;display:flex;align-items:center;justify-content:center}
</style>
</head>
<body>

<header class="site-header abs"></header>
<div class="brand abs">Meridale<br>Real<br>Estate</div>
<div class="ctrl search-field abs">Search :
  <svg width="9" height="9" viewBox="0 0 10 10"><circle cx="4" cy="4" r="3" fill="none" stroke="#888" stroke-width="1.2"/><path d="M6.3 6.3L9 9" stroke="#888" stroke-width="1.3"/></svg></div>
<div class="ctrl btn-login abs">Login
  <svg width="7" height="7" viewBox="0 0 8 8"><path d="M1 2.5l3 3 3-3" fill="none" stroke="#666" stroke-width="1.1"/></svg></div>
<div class="ctrl btn-register abs">Register
  <svg width="7" height="7" viewBox="0 0 8 8"><path d="M1 2.5l3 3 3-3" fill="none" stroke="#666" stroke-width="1.1"/></svg></div>
<div class="ctrl btn-help abs">Help
  <svg width="7" height="7" viewBox="0 0 8 8"><path d="M1 2.5l3 3 3-3" fill="none" stroke="#666" stroke-width="1.1"/></svg></div>

<section>
  <div class="hero abs" role="img" aria-label="Modern stone house with lit windows at dusk"></div>
  <div class="hero-arrow abs" style="left:50px"></div>
  <div class="hero-arrow abs" style="left:704px"></div>
  <form class="search-mask abs">
    <h2>SEARCH MASK</h2>
    <div class="mask-select abs" style="left:87px">SERVICE :
      <svg width="5" height="9" viewBox="0 0 5 9"><path d="M.5 3.5L2.5 1l2 2.5M.5 5.5L2.5 8l2-2.5" fill="none" stroke="#666"/></svg></div>
    <div class="mask-select abs" style="left:214px">DATE TO CHOOSE
      <svg width="5" height="9" viewBox="0 0 5 9"><path d="M.5 3.5L2.5 1l2 2.5M.5 5.5L2.5 8l2-2.5" fill="none" stroke="#666"/></svg></div>
    <div class="mask-select abs" style="left:341px">HOURS NEEDED
      <svg width="5" height="9" viewBox="0 0 5 9"><path d="M.5 3.5L2.5 1l2 2.5M.5 5.5L2.5 8l2-2.5" fill="none" stroke="#666"/></svg></div>
    <div class="mask-submit abs">Search</div>
  </form>
</section>

<section>
  <div class="welcome-photo abs" role="img" aria-label="Contemporary villa with pool at twilight"></div>
  <h1 class="welcome-title abs">Welcome to Pros by the Hour</h1>
  <p class="welcome-text abs">Meridale Real Estate changes the way homes are listed. Instead of a large commission taken at closing, you book top level professional real estate services by the hour and pay only for the time you actually use. Need a pricing review, listing photos, a staged open house or a contract check? Pick the service, choose a date and set the hours you need. Our licensed agents handle the rest with the same care a full-service brokerage offers, at a fraction of the usual cost, so more of your sale stays with you.</p>
  <div class="divider abs"></div>
</section>

<section>
  <h2 class="section-title offers-title abs">Special offers</h2>
  <p class="lead offers-lead abs">Book any of our professional listing services by the hour. Each package is led by an experienced local agent and can be extended whenever you need more time, with no commission taken at closing and no long contract to sign...</p>
  <svg class="pager abs" style="left:650px" width="22" height="10" viewBox="0 0 22 10"><path d="M5 1L1 5l4 4M17 1l4 4-4 4" fill="none" stroke="#999" stroke-width="1.2"/></svg>

  <article class="offer abs" style="left:112px">
    <div class="photo" role="img" aria-label="Mansion with pool at sunset" style="background:linear-gradient(180deg,#e7a88c,#c9705a 45%,#3aa0c4 85%)"></div>
    <h3>Pricing Review</h3><p>Market analysis and a listing price from a local agent, 2 hours...</p><div class="read">Read More</div>
  </article>
  <article class="offer abs" style="left:255px">
    <div class="photo" role="img" aria-label="Suburban house with lawn" style="background:linear-gradient(180deg,#d9dde2,#8e8775 45%,#5a8a3a 85%)"></div>
    <h3>Listing Photos</h3><p>Professional photos and a written listing ready to publish, 3 hours...</p><div class="read">Read More</div>
  </article>
  <article class="offer abs" style="left:399px">
    <div class="photo" role="img" aria-label="Minimal white pavilion under cloudy sky" style="background:linear-gradient(180deg,#6f767a,#9b8e7c 50%,#e9e9e6 85%)"></div>
    <h3>Open House</h3><p>An agent hosts your open house and follows up with visitors, 4 hours...</p><div class="read">Read More</div>
  </article>
  <article class="offer abs" style="left:544px">
    <div class="photo" role="img" aria-label="Brick family home with white trim" style="background:linear-gradient(180deg,#cfd9e6,#6c6762 50%,#4f6b45 90%)"></div>
    <h3>Contract Check</h3><p>Offer review and negotiation support until the deal closes, 2 hours...</p><div class="read">Read More</div>
  </article>
</section>

<section>
  <div class="testimonials abs"></div>
  <h2 class="section-title testimonials-title abs">Testimonials</h2>
  <p class="lead testimonials-lead abs">Sellers across the city have saved thousands by paying only for the hours they need. Here is what a few of them say about listing their homes with our agents on a simple hourly basis instead of a full commission...</p>
  <div class="t-rule abs"></div>
  <svg class="abs" style="left:83px;top:975px" width="10" height="14" viewBox="0 0 10 14"><path d="M8 1L2 7l6 6" fill="none" stroke="rgba(255,255,255,.6)" stroke-width="2"/></svg>
  <svg class="abs" style="left:685px;top:975px" width="10" height="14" viewBox="0 0 10 14"><path d="M2 1l6 6-6 6" fill="none" stroke="rgba(255,255,255,.6)" stroke-width="2"/></svg>

  <div class="avatar abs" style="left:119px;background:radial-gradient(circle,#d8d4c2,#f3f2ee)" role="img" aria-label="Blurred building facade"></div>
  <blockquote class="quote abs" style="left:205px">
    <h4>Dorian Pratt</h4><time>Posted on 27 Mar 2014</time>
    <p>we sold our home in three weeks and paid for just twelve hours of agent time. Clear, simple and far cheaper than a commission</p>
  </blockquote>
  <div class="avatar abs" style="left:415px;background:radial-gradient(circle,#b5a48c,#5b7fb8 70%,#e8ecf2)" role="img" aria-label="Small house model held in hands"></div>
  <blockquote class="quote abs" style="left:501px">
    <h4>Dorian Pratt</h4><time>Posted on 27 Mar 2014</time>
    <p>booking a pricing review by the hour was easy. The agent was sharp, honest and we only paid for the time we really used</p>
  </blockquote>
</section>

<footer>
  <div class="site-footer abs"></div>
  <nav class="foot-col abs" style="left:118px"><h5>About Us</h5><ul><li>Who We Are</li><li>Careers</li><li>Site Map</li><li>Avoid Scams &amp; Fraud</li><li>Contact Us</li></ul></nav>
  <nav class="foot-col abs" style="left:234px"><h5>For Sellers</h5><ul><li>Seller Resources</li><li>Hourly Pricing</li><li>Listing Services</li><li>Homes for Sale</li><li>Mobile Apps</li></ul></nav>
  <nav class="foot-col abs" style="left:369px"><h5>For Agents</h5><ul><li>Who We Are</li><li>Careers</li><li>Site Map</li><li>Avoid Scams &amp; Fraud</li><li>Contact Us</li></ul></nav>
  <nav class="foot-col abs" style="left:486px"><h5>For Buyers</h5><ul><li>Book an Agent</li><li>For Sale By Owner</li><li>Open House Help</li><li>Rentnest Blog</li></ul></nav>
  <ul class="social abs">
    <li><i></i>: Facenote</li>
    <li><i></i>: Linkpro</li>
    <li><i></i>: Circles Plus</li>
    <li><i></i>: Viewtube</li>
  </ul>
  <div class="footer-base abs">© Copyrights 2015 Meridale Real Estate. All Right Reserved</div>
</footer>

</body>
</html>
```